Homemaking training schools needs a Business Card design

Designer, Hello!

No special requirements, good-looking enough.
--------------------------------------------------------------------------

Name: Marcus Dole
Chairman
Tel: 0574-71948263
Mobile: 13857420916
Email: kelvora@mailnest.example
Web: www.prt2019.example
Add: No.258, LanpingJie, BeiyuanQu, Ningbo, Zhejiang

LOGO
Ningbo PRT Homemaking Training School

Target Market(s)

pregnant women, mothers, infants, the elderly and families, including cleaning, cooking, nursing training.

Industry/Entity Type

Business

Contact Information for Business Card

Name: Marcus Dole
Chairman
Tel: 0574-71948263
Mobile: 13857420916
Email: kelvora@mailnest.example
Web: www.prt2019.example

LOGO

Font styles to use
Serif
Sans Serif
Decorative

Requirements
Nice to have
• Feels: clean, specifications, safety, comfort, warmth and happiness.

```html
<!DOCTYPE html>
<html lang="en">
<head>
<meta charset="utf-8">
<title>PinRuiTang Business Card</title>
<link href="https://fonts.googleapis.com/css2?family=Bebas+Neue&family=Nunito:wght@400&family=Open+Sans:wght@400;600&display=swap" rel="stylesheet">
<style>
  :root {
    --backdrop: #e9e6e2;
    --card-dark: #000000;
    --card-light: #ffffff;
    --brand-blue: #1e78c2;
    --brand-pink: #e0168a;
    --ink: #111111;
    --soft-white: #e6e6e6;
  }
  html, body {
    margin: 0;
    padding: 0;
    width: 1200px;
    height: 1000px;
    overflow: hidden;
    background: var(--backdrop);
  }
  .canvas {
    position: relative;
    width: 1200px;
    height: 1000px;
  }
  .card {
    position: absolute;
    left: 265px;
    width: 665px;
    border-radius: 24px;
    box-shadow: 0 4px 10px rgba(0,0,0,0.25);
  }
  .card--front {
    top: 73px;
    height: 397px;
    background: var(--card-dark);
  }
  .card--back {
    top: 532px;
    height: 398px;
    background: var(--card-light);
  }
  .brand-name {
    position: absolute;
    left: 265px;
    width: 665px;
    top: 262px;
    text-align: center;
    font-family: "Open Sans", sans-serif;
    font-weight: 600;
    font-size: 50px;
    line-height: 60px;
    color: var(--soft-white);
    margin: 0;
  }
  .tagline {
    position: absolute;
    top: 328px;
    left: 397px;
    width: 403px;
    display: flex;
    align-items: center;
    gap: 8px;
    font-family: "Nunito", sans-serif;
    font-size: 23px;
    line-height: 30px;
    color: var(--soft-white);
    white-space: nowrap;
  }
  .tagline::before,
  .tagline::after {
    content: "";
    flex: 1;
    height: 2px;
    background: var(--soft-white);
  }
  .front-web {
    position: absolute;
    top: 423px;
    left: 265px;
    width: 665px;
    text-align: center;
    font-family: "Open Sans", sans-serif;
    font-size: 15px;
    color: #cfcfcf;
  }
  .person {
    position: absolute;
    top: 702px;
    right: 620px;
    text-align: right;
  }
  .person__name {
    font-family: "Bebas Neue", sans-serif;
    font-size: 38px;
    line-height: 34px;
    color: var(--ink);
  }
  .person__role {
    font-family: "Open Sans", sans-serif;
    font-size: 16px;
    line-height: 22px;
    color: var(--brand-pink);
    margin-top: 2px;
  }
  .divider {
    position: absolute;
    left: 597px;
    top: 685px;
    width: 2px;
    height: 89px;
    background: var(--ink);
  }
  .contacts {
    position: absolute;
    left: 614px;
    top: 685px;
    margin: 0;
    padding: 0;
    list-style: none;
    font-family: "Open Sans", sans-serif;
    font-size: 16px;
    color: var(--ink);
  }
  .contacts li {
    display: flex;
    align-items: center;
    height: 22.5px;
    gap: 6px;
  }
  .contacts svg {
    width: 16px;
    height: 16px;
    fill: var(--brand-blue);
  }
  .address {
    position: absolute;
    top: 880px;
    left: 265px;
    width: 665px;
    text-align: center;
    font-family: "Open Sans", sans-serif;
    font-size: 16px;
    color: var(--ink);
  }
</style>
</head>
<body>
<div class="canvas">
  <section class="card card--front"></section>
  <p class="brand-name">PinRuiTang</p>
  <div class="tagline">Training &amp; Services</div>
  <div class="front-web">www.prt2019.example</div>

  <section class="card card--back"></section>
  <div class="person">
    <div class="person__name">MARCUS DOLE</div>
    <div class="person__role">Chairman</div>
  </div>
  <div class="divider"></div>
  <ul class="contacts">
    <li>
      <svg viewBox="0 0 16 16" aria-hidden="true"><path d="M4 1h8v14H4z M5 2v9h6V2z M7 12.5h2v1H7z" fill-rule="evenodd"/></svg>
      0574-71948263
    </li>
    <li>
      <svg viewBox="0 0 16 16" aria-hidden="true"><path d="M1 6c0-2 3-3 7-3s7 1 7 3v1h-3V5.5H4V7H1z M3 8h10l1 6H2z"/></svg>
      13857420916
    </li>
    <li>
      <svg viewBox="0 0 16 16" aria-hidden="true"><path d="M1 3h14v10H1z M2 4.2v.6l6 4 6-4v-.6z" fill-rule="evenodd"/></svg>
      kelvora@mailnest.example
    </li>
    <li>
      <svg viewBox="0 0 16 16" aria-hidden="true"><circle cx="7" cy="7" r="6"/><path d="M8 8l7 3-3 1-1 3z" fill="#fff" stroke="#1e78c2" stroke-width="1"/></svg>
      www.prt2019.example
    </li>
  </ul>
  <div class="address">No.258, LanpingJie, BeiyuanQu, Ningbo, Zhejiang</div>
</div>
</body>
</html>
```